Card Design for my dog training business Brightpaw Obedience

Need a business card design for my dog training business with my new logo. Want the card to come off professional yet fun. Want it to be very eye catchy as well. I normally have these at vet clinics, pet stores, and groomers. so need it to look better than my competitors.
Target Market(s)
dog owners
Industry/Entity Type
Dog Training
Contact Information for Business Card
needs logo, my name and info
Font styles to use
Serif
Colors
0255a3
ffffff
ec1f27
000000
333333
fbfbfb
Requirements
Must have
- Brightpaw Obedience
- Felix Orland
- 415 903 2276
- info@brightpawobedience.example
- www.brightpawobedience.example

```html
<!DOCTYPE html>
<html lang="en">
<head>
<meta charset="utf-8">
<title>Brightpaw Obedience – Business Card</title>
<link rel="stylesheet" href="https://fonts.googleapis.com/css2?family=Roboto:wght@400;700&family=Crimson+Text:ital@1&display=swap">
<style>
  :root {
    --ink: #2b2a2a;
    --paper: #ffffff;
    --stage: #e8e5e0;
    --soft: #fbfbfb;
    --shadow: rgba(0,0,0,0.25);
  }
  * { margin: 0; padding: 0; box-sizing: border-box; }
  html, body { width: 1200px; height: 1040px; overflow: hidden; }
  body {
    background: var(--stage);
    display: flex; flex-direction: column; align-items: center; justify-content: center;
    gap: 60px;
    font-family: "Roboto", Arial, sans-serif;
  }
  .card {
    position: relative; width: 700px; height: 400px; overflow: hidden;
    box-shadow: 0 10px 28px var(--shadow);
  }
  .card-front { background: var(--paper); }
  .card-back { background: var(--ink); }
  .swoosh { position: absolute; inset: 0; }
  .contact {
    position: absolute; top: 46px; right: 300px; text-align: right; color: var(--paper);
  }
  .contact-name { font-weight: 700; font-size: 30px; margin-bottom: 14px; letter-spacing: .2px; }
  .contact-line {
    display: flex; justify-content: flex-end; align-items: center; gap: 8px;
    font-size: 15px; line-height: 24px;
  }
  .contact-line svg { width: 14px; height: 14px; fill: var(--paper); }
  .brand-mark {
    position: absolute; right: 48px; bottom: 58px;
    font-weight: 700; font-size: 26px; color: var(--ink);
  }
  .brand-mark-large {
    position: absolute; left: 0; right: 0; top: 140px; text-align: center;
    font-weight: 700; font-size: 44px; color: var(--paper);
  }
  .tagline {
    position: absolute; left: 0; right: 0; bottom: 46px; text-align: center;
    font-family: "Crimson Text", Georgia, serif; font-style: italic;
    font-size: 20px; color: var(--soft);
  }
</style>
</head>
<body>
  <section class="card card-front">
    <svg class="swoosh" viewBox="0 0 700 400" aria-hidden="true">
      <path d="M0 0 H660 C540 30 470 150 360 260 C280 340 170 385 0 392 Z" fill="var(--ink)"/>
      <path d="M676 8 C556 44 486 162 376 272 C296 352 186 397 0 404" fill="none" stroke="var(--ink)" stroke-width="2"/>
    </svg>
    <div class="contact">
      <p class="contact-name">Felix Orland</p>
      <p class="contact-line">415 903 2276
        <svg viewBox="0 0 24 24"><path d="M6.6 10.8a15.2 15.2 0 0 0 6.6 6.6l2.2-2.2a1 1 0 0 1 1-.25 11.4 11.4 0 0 0 3.6.57 1 1 0 0 1 1 1V20a1 1 0 0 1-1 1A17 17 0 0 1 3 4a1 1 0 0 1 1-1h3.5a1 1 0 0 1 1 1c0 1.25.2 2.45.57 3.57a1 1 0 0 1-.25 1z"/></svg></p>
      <p class="contact-line">info@brightpawobedience.example
        <svg viewBox="0 0 24 24"><path d="M2 5h20v14H2z M4 7v.5l8 5 8-5V7l-8 5z" fill-rule="evenodd"/></svg></p>
      <p class="contact-line">www.brightpawobedience.example
        <svg viewBox="0 0 24 24"><path d="M12 2a10 10 0 1 0 0 20 10 10 0 0 0 0-20zm0 2c1.3 1.5 2.2 3.6 2.4 7H9.6c.2-3.4 1.1-5.5 2.4-7zm-4.4 7H4.1a8 8 0 0 1 5-6.4c-.9 1.7-1.4 3.900-1.5 6.4zm0 2c.1 2.5.6 4.7 1.5 6.4a8 8 0 0 1-5-6.4zm2 0h4.8c-.2 3.4-1.1 5.5-2.4 7-1.3-1.5-2.200-3.6-2.4-7zm6.8 0h3.5a8 8 0 0 1-5 6.4c.9-1.7 1.4-3.9 1.5-6.4zm0-2c-.1-2.5-.6-4.700-1.5-6.4a8 8 0 0 1 5 6.4z"/></svg></p>
    </div>
    <p class="brand-mark">Brightpaw Obedience</p>
  </section>

  <section class="card card-back">
    <p class="brand-mark-large">Brightpaw Obedience</p>
    <p class="tagline">“Helping good dogs become great companions.”</p>
  </section>
</body>
</html>
```